Small Business Broker Business Card Design

A business card design for a small business brokerage, which is a financial service, not unlike real estate brokerage, but for small businesses such as laundromats, pizza shops, restaurants, cleaners etc. The designs should all be simple, more conservative in nature, using the colors and font of the logo. Again, think real estate Brokerage as a business context
Contact Information for Business Card
Name: Glen R. Harlow. Title: Small Business Advisor. Email: g.harlow@bayfieldcapitalworks.example. Mobile: (555) 274-3918. Office: (555) 806-2147. www.bayfieldcapitalworks.example

```html
<!DOCTYPE html>
<html lang="en">
<head>
<meta charset="utf-8">
<title>Bayfield Capital Works – Business Card</title>
<link href="https://fonts.googleapis.com/css2?family=Montserrat:wght@400;500;600;700&display=swap" rel="stylesheet">
<style>
  :root {
    --navy: #1c3a6e;
    --navy-deep: #173260;
    --navy-soft: #25477d;
    --green: #8bc43f;
    --ink: #2b2b2b;
    --paper: #f3f3f3;
    --stage: #1e1e1e;
  }
  * { margin: 0; padding: 0; box-sizing: border-box; }
  html, body {
    width: 1200px; height: 1059px; overflow: hidden;
    background: var(--stage);
    font-family: "Montserrat", sans-serif;
  }
  .canvas { position: relative; width: 1200px; height: 1059px; }

  .card { position: absolute; left: 255px; width: 690px; height: 392px; overflow: hidden; }

  /* Front */
  .card--front { top: 89px; background: var(--paper); color: var(--ink); }
  .brand {
    position: absolute; right: 36px; top: 40px;
    text-align: center;
  }
  .brand__mark { display: block; width: 72px; height: 72px; margin: 0 auto 16px; background: var(--navy); }
  .brand__name { font-size: 15.5px; font-weight: 700; color: var(--navy); letter-spacing: 0.2px; white-space: nowrap; line-height: 1.1; }
  .brand__tagline { font-size: 7.6px; font-weight: 600; color: var(--green); letter-spacing: 1.15px; margin-top: 3px; white-space: nowrap; }

  .person { position: absolute; left: 36px; top: 163px; }
  .person__name { font-size: 31px; font-weight: 700; letter-spacing: 0.2px; line-height: 1; white-space: nowrap; }
  .person__first { color: var(--navy); }
  .person__last { color: var(--green); }
  .person__title { font-size: 16px; font-weight: 400; margin-top: 5px; }

  .divider { position: absolute; left: 36px; right: 36px; top: 237px; height: 1px; background: var(--navy); }

  .contacts { position: absolute; left: 36px; top: 258px; list-style: none; }
  .contacts li { display: flex; align-items: center; height: 26px; font-size: 15.5px; white-space: nowrap; }
  .contacts svg { width: 13px; height: 13px; margin-right: 9px; fill: var(--green); flex: none; }

  .address { position: absolute; right: 36px; top: 313px; text-align: right; font-size: 15.5px; line-height: 22px; white-space: nowrap; }

  .footer-band { position: absolute; left: 0; bottom: 0; width: 690px; height: 13px; }

  /* Back */
  .card--back {
    top: 546px;
    background: linear-gradient(160deg, var(--navy-soft) 0%, var(--navy-deep) 55%, var(--navy-soft) 100%);
    text-align: center; color: #fff;
  }
  .card--back .brand__mark { position: absolute; left: 277px; top: 100px; width: 136px; height: 136px; margin: 0; background: #fff; }
  .back__name { position: absolute; left: 0; right: 0; top: 254px; font-size: 26px; font-weight: 700; letter-spacing: 0.4px; white-space: nowrap; }
  .back__tagline { position: absolute; left: 0; right: 0; top: 287px; font-size: 13px; font-weight: 600; color: var(--green); letter-spacing: 2.2px; white-space: nowrap; }
</style>
</head>
<body>
<main class="canvas">

  <section class="card card--front">
    <div class="brand">
      <span class="brand__mark"></span>
      <div class="brand__name">BAYFIELD CAPITAL WORKS, INC</div>
      <div class="brand__tagline">STEADY ADVICE FOR NEIGHBORHOOD BUSINESS DEALS</div>
    </div>

    <div class="person">
      <div class="person__name"><span class="person__first">GLEN</span> <span class="person__last">R. HARLOW</span></div>
      <div class="person__title">Owner &amp; Manager</div>
    </div>

    <div class="divider"></div>

    <ul class="contacts">
      <li><svg viewBox="0 0 16 16"><path d="M1 6c0-2 3-4 7-4s7 2 7 4l-1 1-3-1V4.5C9.5 4 6.5 4 5 4.5V6L2 7z"/><rect x="3" y="8" width="10" height="6" rx="1"/></svg>(555) 806-2147</li>
      <li><svg viewBox="0 0 16 16"><path d="M4.5 0h7a1.5 1.5 0 0 1 1.5 1.5v13a1.5 1.5 0 0 1-1.5 1.5h-7A1.5 1.5 0 0 1 3 14.5v-13A1.5 1.5 0 0 1 4.5 0zM5 2v10h6V2zm3 11a1 1 0 1 0 0 2 1 1 0 0 0 0-2z"/></svg>(555) 274-3918</li>
      <li><svg viewBox="0 0 16 16"><path d="M8 1l7 5v9H1V6zm0 2L3 6.5 8 10l5-3.5z"/></svg>g.harlow@bayfieldcapitalworks.example</li>
      <li><svg viewBox="0 0 16 16"><circle cx="8" cy="8" r="7"/><path d="M4 5l3 1-1 3 2 2-1 3M11 3l-1 3 3 2" stroke="#f3f3f3" stroke-width="1.3" fill="none"/></svg>www.bayfieldcapitalworks.example</li>
    </ul>

    <div class="address">
      P.O. Box 418 Harbor Lane<br>
      Bayfield AB, T4B 208
    </div>

    <svg class="footer-band" viewBox="0 0 690 13" preserveAspectRatio="none">
      <polygon points="0,0 352,0 330,13 0,13" fill="var(--navy)"/>
      <polygon points="362,0 690,0 690,13 340,13" fill="var(--green)"/>
    </svg>
  </section>

  <section class="card card--back">
    <span class="brand__mark"></span>
    <div class="back__name">BAYFIELD CAPITAL WORKS, INC</div>
    <div class="back__tagline">STEADY ADVICE FOR NEIGHBORHOOD BUSINESS DEALS</div>
  </section>

</main>
</body>
</html>
```